Talvane Capital LLC

Need Professional Business cards for New Investment Fund

Target Market(s)

High Quality investors

Industry/Entity Type

Financial

Contact Information for Business Card

Phone Number +1 555 284 6190
Name Lukas Varenko
Title Fund Manager
email lv@FundTalvane.com
Website www.FundTalvane.com

Colors

Designer to choose colors to be used in the design.

Requirements
Must have
• Must have our Logo and all of the above. Must be made so lettering and loge can be raised

```html
<!DOCTYPE html>
<html lang="en">
<head>
<meta charset="utf-8">
<title>Talvane Capital LLC – Business Card</title>
<link rel="stylesheet" href="https://fonts.googleapis.com/css2?family=Jost:wght@400;500&display=swap">
<style>
  :root {
    --backdrop: #d9d9d9;
    --card-white: #ffffff;
    --slate: #474f47;
    --lime: #22ee00;
  }
  html, body {
    margin: 0;
    padding: 0;
    width: 1200px;
    height: 1200px;
    overflow: hidden;
    background: var(--backdrop);
    font-family: "Jost", "Futura", sans-serif;
  }
  .sheet {
    position: relative;
    width: 1200px;
    height: 1200px;
  }
  .card {
    position: absolute;
    left: 160px;
    width: 880px;
    height: 503px;
    display: block;
  }
  .card--front { top: 70px; }
  .card--back { top: 627px; }
  .holder-name { fill: var(--lime); font-size: 26px; font-weight: 400; }
  .holder-title { fill: #ffffff; font-size: 18px; }
  .contact-line { fill: #ffffff; font-size: 17px; }
  .contact-icon { fill: var(--lime); }
  .brand-name { font-size: 40px; font-weight: 500; letter-spacing: 2px; fill: var(--slate); }
</style>
</head>
<body>
<main class="sheet">

  <svg class="card card--front" viewBox="0 0 800 457" aria-label="Business card front">
    <rect class="card-face" width="800" height="457" fill="var(--card-white)"/>
    <polygon class="info-panel" points="0,263 297,263 456,457 0,457" fill="var(--slate)"/>
    <polygon class="accent-band" points="475,420 800,420 800,457 456,457" fill="var(--lime)"/>

    <g class="brand-lockup">
      <rect x="530" y="214" width="20" height="20" fill="var(--lime)"/>
      <text class="brand-name" x="562" y="234">TALVANE</text>
    </g>

    <text class="holder-name" x="41" y="313">Lukas Varenko</text>
    <text class="holder-title" x="41" y="338">Fund Manager</text>

    <g class="contact-icon">
      <path d="M44 366 q2 -2 4 0 l2 3 q1 2 -1 3 q1 3 4 5 q1 -2 3 -1 l3 2 q2 2 0 4 q-3 3 -8 -1 q-5 -4 -7 -9 q-1 -4 0 -6z"/>
      <rect x="43" y="392" width="14" height="10" rx="1"/>
      <circle cx="50" cy="420" r="7"/>
    </g>
    <path d="M43 392 l7 6 l7 -6" stroke="var(--slate)" stroke-width="1.2" fill="none"/>
    <path d="M43 420 h14 M50 413 q-4 7 0 14 M50 413 q4 7 0 14" stroke="var(--slate)" stroke-width="1" fill="none"/>

    <text class="contact-line" x="67" y="378">+1 555 284 6190</text>
    <text class="contact-line" x="67" y="402">lv@FundTalvane.com</text>
    <text class="contact-line" x="67" y="424">www.FundTalvane.com</text>
  </svg>

  <svg class="card card--back" viewBox="0 0 800 457" aria-label="Business card back">
    <rect class="card-face" width="800" height="457" fill="var(--lime)"/>
    <g class="brand-lockup">
      <rect x="290" y="225" width="20" height="20" fill="var(--slate)"/>
      <text class="brand-name" x="322" y="245">TALVANE</text>
    </g>
  </svg>

</main>
</body>
</html>
```